Business Card Design Project

After recently finishing a design project for the company logo using markbazaar, it's now time for a business card. Attached to this is the logo.

The requirements for the business card are pretty straightforward:

- A clean, uncomplicated look
- Consistent usage of fonts
- Designs for both single sided and double sided cards
- A modern layout with preferably space to refer to social media accounts and/or downloadable vcards through a qr code
- consistent application of the company colour scheme: red/white. Hex codes for exact colour can be provided

Thanks!

```html
<!DOCTYPE html>
<html lang="en">
<head>
<meta charset="utf-8">
<title>Kiln Row Recruiting – Business Cards</title>
<link rel="stylesheet" href="https://fonts.googleapis.com/css2?family=Source+Sans+3:ital,wght@0,400;0,600;0,700;1,700&display=swap">
<style>
  :root {
    --brand-red: #e3202a;
    --accent-grey: #a3a3a3;
    --ink: #2b2a29;
    --card: #ffffff;
    --backdrop: #ebe8e4;
  }
  * { box-sizing: border-box; margin: 0; padding: 0; }
  html, body {
    width: 960px;
    height: 1200px;
    overflow: hidden;
    background: var(--backdrop);
    font-family: "Source Sans 3", "Myriad Pro", Arial, sans-serif;
    color: var(--ink);
  }
  .card {
    position: absolute;
    left: 60px;
    width: 840px;
    height: 480px;
    background: var(--card);
    border-radius: 36px;
    overflow: hidden;
    box-shadow: 0 6px 14px rgba(0,0,0,0.18);
  }
  .card--front { top: 63px; }
  .card--back { top: 638px; }
  .card__corners {
    position: absolute;
    inset: 0;
    width: 840px;
    height: 480px;
  }
  .wordmark {
    position: absolute;
    display: flex;
    align-items: center;
    gap: 22px;
    white-space: nowrap;
  }
  .wordmark__square {
    width: 44px;
    height: 44px;
    background: var(--brand-red);
  }
  .wordmark__name {
    font-size: 62px;
    font-weight: 600;
    letter-spacing: -1px;
    color: var(--ink);
  }
  .card--front .wordmark { left: 172px; top: 140px; }
  .card--back .wordmark { left: 138px; top: 200px; }
  .card--back .wordmark__name { font-size: 68px; }

  .holder {
    position: absolute;
    left: 0; right: 0;
    top: 336px;
    text-align: center;
    font-size: 20px;
  }
  .holder__name { font-size: 25px; font-weight: 700; }
  .contact {
    position: absolute;
    left: 0; right: 0;
    top: 394px;
    text-align: center;
    font-size: 20px;
    line-height: 29px;
  }
  .label { font-weight: 700; font-style: italic; }
  .sep { margin: 0 8px; }

  .back-info {
    position: absolute;
    top: 94px;
    font-size: 20px;
    line-height: 29px;
  }
  .back-info--web { left: 187px; }
  .back-info--address { left: 526px; }
</style>
</head>
<body>

<section class="card card--front" aria-label="Card front">
  <svg class="card__corners" viewBox="0 0 840 480" aria-hidden="true">
    <path d="M712 0 Q812 38 840 128 L840 0 Z" fill="var(--brand-red)"/>
    <path d="M700 0 Q806 44 840 140" fill="none" stroke="var(--accent-grey)" stroke-width="5"/>
    <path d="M0 350 Q22 440 104 480 L0 480 Z" fill="var(--brand-red)"/>
    <path d="M0 336 Q28 446 120 480" fill="none" stroke="var(--accent-grey)" stroke-width="5"/>
  </svg>

  <div class="wordmark">
    <span class="wordmark__square"></span>
    <span class="wordmark__name">Kiln Row Recruiting</span>
  </div>

  <p class="holder"><span class="holder__name">Your Name -</span> Designation</p>

  <div class="contact">
    <p><span class="label">t</span> : 123-123-1234<span class="sep">|</span>1234, Street Name, District, City, Country Code.</p>
    <p><span class="label">e</span> : info@yourwebsite.com<span class="sep">|</span><span class="label">w</span> : www.kilnrow.com</p>
  </div>
</section>

<section class="card card--back" aria-label="Card back">
  <div class="back-info back-info--web">
    <p><span class="label">e</span> : info@yourwebsite.com</p>
    <p><span class="label">w</span> : www.kilnrow.com</p>
  </div>
  <div class="back-info back-info--address">
    <p>1234, Street Name</p>
    <p>District, City, Country Code.</p>
  </div>

  <div class="wordmark">
    <span class="wordmark__square"></span>
    <span class="wordmark__name">Kiln Row Recruiting</span>
  </div>
</section>

</body>
</html>
```